i need a business card for a plumbing company in california

we are a drain cleaning , maintenance plumbing company who is starting new marketing campaign for a tatrench-less pipe installation department .

Target Market(s)

the professional who appreciates time and quality workmanship.

Industry/Entity Type

Plumbing

Colors
0655a3
ec1f27

Requirements
Must have
• the second logo needs to be included
Nice to have
• a focus on the services offered
Should not have
• any underlined words on the brief

```html
<!DOCTYPE html>
<html lang="en">
<head>
<meta charset="utf-8">
<title>Clearline Plumbing – Business Card</title>
<link rel="stylesheet" href="https://fonts.googleapis.com/css2?family=Arimo:wght@400;700&display=swap">
<style>
  :root {
    --page-bg: #ebe8e4;
    --card-grey: #7b7870;
    --card-red: #e0242a;
    --badge-white: #f3f3f2;
    --badge-edge: #e2e2e0;
    --text-light: #ffffff;
    --logo-grey: #7a776f;
  }
  * { margin: 0; padding: 0; box-sizing: border-box; }
  html, body {
    width: 1200px;
    height: 900px;
    overflow: hidden;
    background: var(--page-bg);
    font-family: "Arimo", Arial, sans-serif;
  }
  .business-card {
    position: absolute;
    left: 120px;
    top: 154px;
    width: 960px;
    height: 592px;
    background: var(--card-grey);
    overflow: hidden;
    box-shadow: 0 18px 40px rgba(0, 0, 0, 0.18);
  }
  .accent-band {
    position: absolute;
    left: 645px;
    top: 0;
    width: 315px;
    height: 100%;
    background: var(--card-red);
  }
  .logo-badge {
    position: absolute;
    left: 398px;
    top: 40px;
    width: 514px;
    height: 514px;
    border-radius: 50%;
    background: radial-gradient(circle at 40% 35%, #ffffff 0%, var(--badge-white) 60%, var(--badge-edge) 100%);
    display: flex;
    align-items: center;
    justify-content: center;
  }
  .brand-name {
    display: flex;
    align-items: center;
    gap: 18px;
    color: var(--logo-grey);
    font-weight: 700;
    font-size: 58px;
    line-height: 1.02;
  }
  .brand-mark {
    width: 34px;
    height: 34px;
    border-radius: 50%;
    background: var(--card-red);
    flex: none;
  }
  .person {
    position: absolute;
    left: 59px;
    top: 74px;
    color: var(--text-light);
  }
  .person-name {
    font-size: 35px;
    font-weight: 400;
    letter-spacing: 0.5px;
    line-height: 1.1;
  }
  .person-role {
    font-size: 26px;
    line-height: 1.3;
  }
  .contact-list {
    position: absolute;
    left: 62px;
    top: 290px;
    list-style: none;
    color: var(--text-light);
    font-size: 26px;
  }
  .contact-item {
    display: flex;
    align-items: center;
    height: 35px;
    white-space: nowrap;
  }
  .contact-icon {
    width: 20px;
    height: 20px;
    margin-right: 10px;
    fill: var(--text-light);
    flex: none;
  }
  .address {
    position: absolute;
    left: 59px;
    top: 458px;
    color: var(--text-light);
    font-size: 26px;
    line-height: 35px;
    font-style: normal;
    white-space: nowrap;
  }
</style>
</head>
<body>
  <main class="business-card">
    <div class="accent-band"></div>

    <div class="logo-badge">
      <div class="brand-name">
        <span>Clearline<br>Plumbing</span>
        <span class="brand-mark"></span>
      </div>
    </div>

    <header class="person">
      <h1 class="person-name">DANIEL REYES</h1>
      <p class="person-role">Managing Director</p>
    </header>

    <ul class="contact-list">
      <li class="contact-item">
        <svg class="contact-icon" viewBox="0 0 20 20" aria-hidden="true">
          <path d="M6 1h8a1.5 1.5 0 0 1 1.5 1.5v15A1.5 1.5 0 0 1 14 19H6a1.5 1.5 0 0 1-1.5-1.5v-15A1.5 1.5 0 0 1 6 1zm0.5 2.5v11h7v-11zM10 15.6a1 1 0 1 0 0 2 1 1 0 0 0 0-2z"/>
        </svg>
        559-555 014 2
      </li>
      <li class="contact-item">
        <svg class="contact-icon" viewBox="0 0 20 20" aria-hidden="true">
          <path d="M2 6c0-2 3-3.5 8-3.5S18 4 18 6v1.5h-4V6H6v1.5H2zM5 9h10l2.5 8h-15zm5 2a2.5 2.5 0 1 0 0 5 2.5 2.5 0 0 0 0-5z"/>
        </svg>
        559-555 019 8
      </li>
      <li class="contact-item">
        <svg class="contact-icon" viewBox="0 0 20 20" aria-hidden="true">
          <path d="M2 4h16v12H2zm1.6 1.4L10 10.5l6.4-5.1zM3.5 14.5h13V7.2L10 12.3 3.5 7.2z"/>
        </svg>
        info@clearline.com
      </li>
      <li class="contact-item">
        <svg class="contact-icon" viewBox="0 0 20 20" aria-hidden="true">
          <path d="M10 1.5a8.5 8.5 0 1 0 0 17 8.5 8.5 0 0 0 0-17zm-1 2.2c-1 1.3-2.5 1.6-2.5 3.3 0 1.4 1.6 1.5 2.4 2.4.8.9 0 2.4.8 3.4.7.9 1.2 2 1 3.5A6.5 6.5 0 0 1 9 3.7zm4.8 2.1c.9.6 1.6 1.3 2.1 2.3-.9-.1-1.8.2-2.3-.5-.3-.5.1-1.2.2-1.8z"/>
        </svg>
        www.clearlineplumb.com
      </li>
    </ul>

    <address class="address">
      2210 Orchard Way, Suite 4<br>
      Fresno, CA 93721.
    </address>
  </main>
</body>
</html>
```